Business Card Design Project - del varosi group

dear Sirs

we need business card design for our group ( DEL Varosi Group ) , i have got the Logo design of our group from pixel harbor in previous , so all need details relating to our group i think available with you, as well as the the chosen logo design

we hope to provide us with business card logo that to be appropaite and satisfactory to us .

thanks

note : logo design of our group is attached .
Updates

Reason: please extend the deadline of my project for additional 15 days because i didn't received appropriate design for our gruop yet . kindly beaware that i have received 77 design till now , supossed to send me 200-250 design at least . thanks

Target Market(s)

contents

name : Kerem EL Nadiri

position : Operation Manager

Industry/Entity Type

Business

Requirements
Must have

• person name

group logo
Nice to have
• logo color matching with back background

```html
<!DOCTYPE html>
<html lang="en">
<head>
<meta charset="utf-8">
<title>DEL Varosi Group – Business Card</title>
<link rel="stylesheet" href="https://fonts.googleapis.com/css2?family=Open+Sans:wght@400;600;700&display=swap">
<style>
  :root {
    --brand-blue: #0d4d91;
    --brand-blue-light: #1566b8;
    --gold: #c9a85a;
    --paper: #ffffff;
    --ink-grey: #555a60;
    --backdrop: #e9e9ea;
  }
  * { box-sizing: border-box; margin: 0; padding: 0; }
  html, body {
    width: 1200px; height: 758px; overflow: hidden;
    background: var(--backdrop);
    font-family: "Open Sans", Arial, sans-serif;
  }
  .canvas {
    position: relative; width: 1200px; height: 758px;
    display: flex; align-items: center; justify-content: center; gap: 60px;
  }
  .card {
    position: relative; width: 530px; height: 303px;
    border-radius: 22px; overflow: hidden;
    box-shadow: 0 6px 18px rgba(0,0,0,0.18);
  }

  /* Front */
  .card--front { background: var(--paper); }
  .front__brand {
    position: absolute; left: 0; right: 0; top: 0; height: 128px;
    display: flex; align-items: center; justify-content: center; gap: 14px;
  }
  .brand-mark {
    width: 22px; height: 22px; background: var(--brand-blue);
  }
  .brand-name {
    font-weight: 700; font-size: 38px; letter-spacing: 1px;
    color: var(--brand-blue); text-transform: uppercase;
  }
  .front__rule { position: absolute; left: 0; right: 0; height: 3px; background: var(--gold); }
  .front__rule--top { top: 136px; }
  .front__rule--bottom { top: 245px; }
  .front__band {
    position: absolute; left: 0; right: 0; top: 142px; height: 100px;
    background: var(--brand-blue);
    display: flex; align-items: center; color: #fff;
  }
  .person { width: 250px; text-align: right; padding-right: 18px; }
  .person__name { font-weight: 700; font-size: 17px; }
  .person__role { font-size: 12px; margin-top: 1px; }
  .band__divider { width: 1px; height: 72px; background: rgba(255,255,255,0.7); }
  .contact-list { list-style: none; padding-left: 14px; font-size: 11.5px; line-height: 15px; }
  .contact-list li { display: flex; align-items: center; gap: 6px; }
  .contact-list svg { width: 9px; height: 9px; fill: #fff; flex: none; }
  .front__address {
    position: absolute; left: 0; right: 0; top: 257px;
    text-align: center; font-size: 13px; color: var(--ink-grey); letter-spacing: 0.3px;
  }

  /* Back */
  .card--back {
    background: linear-gradient(120deg, var(--brand-blue) 0%, var(--brand-blue-light) 100%);
    display: flex; flex-direction: column; align-items: center; justify-content: center;
    color: #fff;
  }
  .card--back .brand-mark { background: #fff; }
  .card--back .brand-name { color: #fff; font-size: 40px; }
  .back__brand { display: flex; align-items: center; gap: 14px; margin-top: -10px; }
  .back__web { margin-top: 46px; font-size: 17px; letter-spacing: 1.5px; }
</style>
</head>
<body>
<main class="canvas">
  <section class="card card--front">
    <div class="front__brand">
      <span class="brand-mark"></span>
      <span class="brand-name">DEL Varosi Group</span>
    </div>
    <div class="front__rule front__rule--top"></div>
    <div class="front__band">
      <div class="person">
        <div class="person__name">Kerem EL Nadiri</div>
        <div class="person__role">Operation Manager</div>
      </div>
      <div class="band__divider"></div>
      <ul class="contact-list">
        <li><svg viewBox="0 0 10 10"><rect x="2.5" y="0.5" width="5" height="9" rx="1"/></svg>+2348130047715</li>
        <li><svg viewBox="0 0 10 10"><path d="M2 0.5 L4 3 L3 4.2 C3.8 5.8 4.5 6.6 5.8 7 L7 6 L9.5 8 L8.5 9.5 C4 9.5 0.5 6 0.5 1.5 Z"/></svg>+2348130047715</li>
        <li><svg viewBox="0 0 10 10"><rect x="0.5" y="4" width="9" height="5.5" rx="1"/><rect x="2.5" y="0.5" width="5" height="3"/></svg>+2348130047715</li>
        <li><svg viewBox="0 0 10 10"><path d="M0.5 2 H9.5 V8.5 H0.5 Z M0.5 2 L5 5.5 L9.5 2" /></svg>name@halvorsuites.com</li>
        <li><svg viewBox="0 0 10 10"><circle cx="5" cy="5" r="4.5"/></svg>www.delvarosi.com</li>
      </ul>
    </div>
    <div class="front__rule front__rule--bottom"></div>
    <p class="front__address">Street name, City, State, zip code</p>
  </section>

  <section class="card card--back">
    <div class="back__brand">
      <span class="brand-mark"></span>
      <span class="brand-name">DEL Varosi Group</span>
    </div>
    <p class="back__web">www.delvarosi.com</p>
  </section>
</main>
</body>
</html>
```